indépendant en tant que Massothérapeute et Préparateur Mental, j'ai besoin de ...

Massothérapeute et préparateur mental indépendant, je recherche une carte de visite sobre et dynamique, sans images liées au massage ou à la préparation mentale mais intégrant mon logo. Les couleurs que j'aime bien sont : Blanc, gris, anthracite, noir et jaune

Contact Information for Business Card

carte de préférence Horizontale
neutre qui puisse toucher le deux domaines Massothérapie et préparation mentale

Requirements
Must have
• mon projet doit intégrer au recto:
LOGO
Loïc Bardèze
078 513 26 48
info@loicbardeze.ch
et éventuellement www.loicbardeze.ch

et au verso les deux adresses:

Chemin des Ormilles 7B
1400 Yverdon-les-Bains

Route de la Gravière 9
1700 Fribourg

Should not have
• mon projet ne doit pas contenir d'image en liens avec le massage ni la préparation mentale.

```html
<!DOCTYPE html>
<html lang="fr">
<head>
<meta charset="utf-8">
<title>Loïc Bardèze – Carte de visite</title>
<link href="https://fonts.googleapis.com/css2?family=Michroma&family=Montserrat:wght@500&family=Arimo:wght@400&display=swap" rel="stylesheet">
<style>
  :root {
    --backdrop: #a8a8a8;
    --anthracite: #231f20;
    --paper: #ffffff;
    --ink: #1c1c1c;
    --silver: #d9dad9;
    --rule: #9c9c9c;
  }
  * { margin: 0; padding: 0; box-sizing: border-box; }
  html, body {
    width: 1200px;
    height: 1200px;
    overflow: hidden;
    background: var(--backdrop);
  }
  .canvas { position: relative; width: 1200px; height: 1200px; }

  .card {
    position: absolute;
    top: 303px;
    height: 594px;
    overflow: hidden;
  }
  .card--front { left: 201px; width: 369px; background: var(--anthracite); }
  .card--back  { left: 599px; width: 364px; background: var(--paper); color: var(--ink); }

  /* Vertical signature on the dark side */
  .signature-vertical {
    position: absolute;
    left: 184px;
    top: 297px;
    transform: translate(-50%, -50%) rotate(-90deg);
    display: flex;
    align-items: center;
    gap: 16px;
    white-space: nowrap;
    color: var(--silver);
  }
  .signature-vertical .mark {
    width: 36px; height: 36px; background: var(--silver); flex: none;
  }
  .signature-vertical .name {
    font-family: "Michroma", sans-serif;
    font-size: 24px;
    line-height: 1;
  }
  .signature-vertical .role {
    font-family: "Montserrat", sans-serif;
    font-weight: 500;
    font-size: 8.5px;
    letter-spacing: 0.6px;
    text-transform: uppercase;
    margin-top: 6px;
  }

  /* Horizontal signature on the white side */
  .signature {
    position: absolute;
    left: 40px;
    top: 131px;
    display: flex;
    align-items: center;
    gap: 12px;
  }
  .signature .mark { width: 30px; height: 30px; background: var(--ink); flex: none; }
  .signature .name {
    font-family: "Michroma", sans-serif;
    font-size: 17px;
    line-height: 1;
  }
  .signature .role {
    font-family: "Montserrat", sans-serif;
    font-weight: 500;
    font-size: 6.6px;
    letter-spacing: 0.4px;
    text-transform: uppercase;
    margin-top: 4px;
  }

  .holder-name {
    position: absolute;
    top: 300px;
    width: 100%;
    text-align: center;
    font-family: "Michroma", sans-serif;
    font-weight: 400;
    font-size: 25px;
    letter-spacing: 1px;
  }

  .contact-icons {
    position: absolute;
    top: 349px;
    left: 0; width: 100%;
    display: flex;
    justify-content: center;
    align-items: center;
    gap: 5px;
  }
  .contact-icons .rule { width: 51px; height: 1px; background: var(--rule); margin: 0 3px; }
  .contact-icons svg { width: 24px; height: 24px; display: block; }

  .text-block {
    position: absolute;
    width: 100%;
    text-align: center;
    font-family: "Arimo", sans-serif;
    font-size: 16.5px;
    line-height: 21.5px;
  }
  .contacts { top: 386px; }
  .divider {
    position: absolute;
    top: 460px;
    left: 89px;
    width: 194px;
    height: 1px;
    background: var(--rule);
  }
  .address--first { top: 470px; }
  .address--second { top: 521px; }
</style>
</head>
<body>
<main class="canvas">

  <section class="card card--front" aria-label="Recto">
    <div class="signature-vertical">
      <span class="mark"></span>
      <div>
        <div class="name">Loïc Bardèze</div>
        <div class="role">Massothérapeute / Préparateur Mental</div>
      </div>
    </div>
  </section>

  <section class="card card--back" aria-label="Verso">
    <div class="signature">
      <span class="mark"></span>
      <div>
        <div class="name">Loïc Bardèze</div>
        <div class="role">Massothérapeute / Préparateur Mental</div>
      </div>
    </div>

    <h1 class="holder-name">LOÏC BARDÈZE</h1>

    <div class="contact-icons">
      <span class="rule"></span>
      <svg viewBox="0 0 24 24" aria-label="Téléphone">
        <rect width="24" height="24" rx="3" fill="#1c1c1c"/>
        <path d="M5 10c0-2 3-3.5 7-3.5s7 1.5 7 3.5v1h-3.5v-1.5h-7V11H5z" fill="#fff"/>
        <path d="M8 12h8l1.5 6h-11z" fill="#fff"/>
        <circle cx="12" cy="15" r="1.6" fill="#1c1c1c"/>
      </svg>
      <svg viewBox="0 0 24 24" aria-label="E-mail">
        <rect width="24" height="24" rx="3" fill="#1c1c1c"/>
        <rect x="5" y="7" width="14" height="10" fill="#fff"/>
        <path d="M5 7l7 6 7-6M5 17l5-5M19 17l-5-5" stroke="#1c1c1c" stroke-width="1" fill="none"/>
      </svg>
      <svg viewBox="0 0 24 24" aria-label="Site web">
        <rect width="24" height="24" rx="3" fill="#1c1c1c"/>
        <circle cx="12" cy="12" r="7" fill="#fff"/>
        <path d="M9 8c1.5 0 2 1.5 1 2.5s-2 1-1.5 3 2 1.5 2 3.5M14 6.5c0 1.5 1.5 2 2.5 3" stroke="#1c1c1c" stroke-width="1.4" fill="none"/>
      </svg>
      <span class="rule"></span>
    </div>

    <p class="text-block contacts">078 513 26 48<br>info@loicbardeze.ch<br>www.loicbardeze.ch</p>
    <span class="divider"></span>
    <p class="text-block address--first">Chemin des Ormilles 7B<br>1400 Yverdon-les-Bains</p>
    <p class="text-block address--second">Route de la Gravière 9<br>1700 Freiburg</p>
  </section>

</main>
</body>
</html>
```